KBT Business Cards

We require business cards for our business. We would like a matte black back to the card, with our logo centred in the middle. The front side of the card is open to design.

Target Market(s)

Clients looking for legal services (professional)

Industry/Entity Type

Legal

Contact Information for Business Card

Doran Kelbrath
Partner
Mobile: 0461 738 524
Email: doran@kbtlaw.co
Website: www.kbtlaw.co
Level 3, 118 Wendmore Street
Sydney NSW 2000

Font styles to use
Other font styles liked:
• Avenir

Colors
f04a50
ffffff
1b1b1b

Requirements
Must have
• Black back with logo included in the centre of the card.
• Our font is Avenir.

```html
<!DOCTYPE html>
<html lang="en">
<head>
<meta charset="utf-8">
<title>KBT Legal – Business Cards</title>
<link href="https://fonts.googleapis.com/css2?family=Nunito+Sans:wght@400;600;700;800&display=swap" rel="stylesheet">
<style>
  :root {
    --ink: #1b1b1b;
    --black: #0b0b0b;
    --paper: #ffffff;
    --crimson: #cf2450;
    --stage: #2b2b2e;
    --muted: #d9d9d9;
  }
  * { margin: 0; padding: 0; box-sizing: border-box; }
  html, body {
    width: 1200px; height: 800px; overflow: hidden;
    background: var(--stage);
    font-family: "Nunito Sans", "Avenir", sans-serif;
  }
  .canvas {
    position: relative; width: 1200px; height: 800px;
    display: flex; align-items: center; justify-content: center; gap: 40px;
  }
  .card {
    position: relative; width: 550px; height: 314px; overflow: hidden;
    box-shadow: 0 18px 40px rgba(0,0,0,.45);
  }

  /* Back */
  .card--back { background: var(--black); color: var(--paper); }
  .brand-lockup {
    position: absolute; left: 50%; top: 50%;
    transform: translate(-50%, -62%);
    display: flex; align-items: center; gap: 14px;
  }
  .brand-mark { width: 22px; height: 22px; background: var(--crimson); }
  .brand-name {
    font-weight: 700; font-size: 34px; letter-spacing: 2px;
    text-transform: uppercase; line-height: 1;
  }
  .card--back .brand-name { color: var(--paper); }
  .back-url {
    position: absolute; left: 0; right: 0; bottom: 74px;
    text-align: center; font-size: 11px; letter-spacing: 3px; color: var(--muted);
  }

  /* Front */
  .card--front { background: var(--paper); color: var(--ink); }
  .front-shapes { position: absolute; inset: 0; }
  .front-brand {
    position: absolute; right: 28px; top: 40px;
    display: flex; align-items: center; gap: 12px;
  }
  .front-brand .brand-name { color: var(--ink); font-size: 30px; }
  .person {
    position: absolute; left: 176px; top: 134px; color: var(--paper);
  }
  .person-name {
    font-weight: 800; font-size: 19px; letter-spacing: .5px;
    text-transform: uppercase; color: var(--crimson); line-height: 1.1;
  }
  .person-role { font-size: 12px; margin-top: 1px; }
  .contact-list { list-style: none; margin-top: 10px; }
  .contact-item {
    display: flex; align-items: center; gap: 8px;
    font-size: 12px; line-height: 17px;
  }
  .contact-icon { width: 12px; height: 12px; flex: none; }
  .address {
    position: absolute; left: 180px; top: 266px;
    font-size: 12.5px; font-weight: 600; line-height: 16px; color: var(--ink);
  }
</style>
</head>
<body>
<main class="canvas">

  <section class="card card--back" aria-label="Card back">
    <div class="brand-lockup">
      <span class="brand-mark"></span>
      <span class="brand-name">KBT Legal</span>
    </div>
    <p class="back-url">www.kbtlaw.co</p>
  </section>

  <section class="card card--front" aria-label="Card front">
    <svg class="front-shapes" viewBox="0 0 550 314" width="550" height="314" aria-hidden="true">
      <polygon fill="var(--crimson)" points="96,196 150,196 164,210 164,314 96,314"/>
      <polygon fill="var(--black)" points="140,118 476,118 436,256 140,256 140,218 156,204 140,190"/>
      <polyline fill="none" stroke="var(--paper)" stroke-width="1.5" points="140,190 156,204 140,218"/>
    </svg>

    <div class="front-brand">
      <span class="brand-mark"></span>
      <span class="brand-name">KBT Legal</span>
    </div>

    <div class="person">
      <p class="person-name">Doran Kelbrath</p>
      <p class="person-role">Partner</p>
      <ul class="contact-list">
        <li class="contact-item">
          <svg class="contact-icon" viewBox="0 0 12 12"><circle cx="6" cy="6" r="5.4" fill="none" stroke="#fff"/><rect x="4" y="2.8" width="4" height="6.4" rx=".8" fill="var(--crimson)"/></svg>
          0461 738 524
        </li>
        <li class="contact-item">
          <svg class="contact-icon" viewBox="0 0 12 12"><circle cx="6" cy="6" r="5.4" fill="none" stroke="#fff"/><rect x="3" y="4" width="6" height="4.2" fill="var(--crimson)"/><polyline points="3,4 6,6.4 9,4" fill="none" stroke="#fff" stroke-width=".7"/></svg>
          doran@kbtlaw.co
        </li>
        <li class="contact-item">
          <svg class="contact-icon" viewBox="0 0 12 12"><circle cx="6" cy="6" r="5.4" fill="none" stroke="#fff"/><circle cx="6" cy="6" r="3" fill="var(--crimson)"/><line x1="3" y1="6" x2="9" y2="6" stroke="#fff" stroke-width=".6"/><ellipse cx="6" cy="6" rx="1.2" ry="3" fill="none" stroke="#fff" stroke-width=".6"/></svg>
          www.kbtlaw.co
        </li>
      </ul>
    </div>

    <p class="address">Level 3, 118 Wendmore Street<br>Sydney NSW 2000</p>
  </section>

</main>
</body>
</html>
```